Corporate Business Card

Very professional, Modern, Not to busy, include phone address email, website
(253) 617-4930, 18761 52nd Avenue S, Kent, WA 98047, martin@plumlinegroup.com, varkoworks.com

Target Market(s)

Manufacturing

Industry/Entity Type

Aero, machining, manufacturing, Off road racing

Contact Information for Business Card

Phone, address email, website

```html
<!DOCTYPE html>
<html lang="en">
<head>
<meta charset="utf-8">
<title>Varko Works – Business Card</title>
<link rel="stylesheet" href="https://fonts.googleapis.com/css2?family=Montserrat:wght@400;500;700;800&display=swap">
<style>
  :root {
    --navy: #17356e;
    --red: #d3222a;
    --white: #ffffff;
    --ink: #1b1b1b;
    --backdrop: #e9eaec;
  }
  * { box-sizing: border-box; margin: 0; padding: 0; }
  html, body {
    width: 1200px; height: 904px; overflow: hidden;
    background: var(--backdrop);
    font-family: "Montserrat", sans-serif;
  }
  .sheet {
    width: 1200px; height: 904px;
    display: flex; flex-direction: column; align-items: center; justify-content: center;
    gap: 34px;
  }
  .card {
    position: relative;
    width: 700px; height: 400px;
    overflow: hidden;
    box-shadow: 0 6px 18px rgba(0,0,0,.18);
  }
  /* Front */
  .card--front { background: var(--navy); }
  .brand {
    position: absolute;
    display: flex; align-items: center; gap: 14px;
  }
  .brand__mark { width: 22px; height: 22px; background: var(--red); }
  .brand__name {
    font-weight: 800; font-size: 58px; letter-spacing: 1px; line-height: 1;
    text-transform: uppercase;
  }
  .brand__rule { position: absolute; height: 2px; }
  .card--front .brand { left: 150px; top: 150px; }
  .card--front .brand__name { color: var(--white); }
  .card--front .brand__rule { left: 186px; top: 236px; width: 230px; background: var(--white); }

  /* Back */
  .card--back { background: var(--white); }
  .card--back .brand { right: 44px; top: 62px; }
  .card--back .brand__mark { width: 16px; height: 16px; }
  .card--back .brand__name { color: var(--navy); font-size: 46px; }
  .card--back .brand__rule { left: 372px; top: 136px; width: 190px; background: var(--navy); }

  .wave { position: absolute; left: 0; top: 0; width: 700px; height: 400px; }

  .contact {
    position: absolute; left: 60px; top: 160px;
    color: var(--ink); font-size: 16px; font-weight: 500; line-height: 1.35;
  }
  .contact__address { margin-bottom: 12px; }
  .contact__list { list-style: none; }
  .contact__item { display: flex; align-items: center; gap: 10px; margin-bottom: 4px; }
  .contact__icon { width: 16px; height: 16px; flex: none; }
</style>
</head>
<body>
<main class="sheet">

  <section class="card card--front" aria-label="Card front">
    <div class="brand">
      <span class="brand__mark"></span>
      <span class="brand__name">Varko Works</span>
    </div>
    <span class="brand__rule"></span>
  </section>

  <section class="card card--back" aria-label="Card back">
    <svg class="wave" viewBox="0 0 700 400" aria-hidden="true">
      <path d="M0 372 C200 368 330 350 430 300 C520 255 600 200 700 190 L700 400 L0 400 Z" fill="var(--navy)"/>
      <path d="M0 352 C200 348 325 330 422 282 C512 237 596 180 700 170 L700 178 C598 188 518 244 428 290 C330 338 202 357 0 361 Z" fill="var(--red)"/>
    </svg>

    <div class="brand">
      <span class="brand__mark"></span>
      <span class="brand__name">Varko Works</span>
    </div>
    <span class="brand__rule"></span>

    <div class="contact">
      <p class="contact__address">18761 52nd Avenue<br>S, Kent, WA 98047</p>
      <ul class="contact__list">
        <li class="contact__item">
          <svg class="contact__icon" viewBox="0 0 16 16"><path fill="var(--red)" d="M1 5c0-2 2-3 7-3s7 1 7 3v1h-4V5H5v1H1zM3 7h10l1 7H2z"/></svg>
          <span>(253) 617-4930</span>
        </li>
        <li class="contact__item">
          <svg class="contact__icon" viewBox="0 0 16 16"><rect x="1" y="3" width="14" height="10" fill="var(--red)"/><path d="M1 3l7 6 7-6" fill="none" stroke="var(--white)" stroke-width="1.3"/></svg>
          <span>martin@plumlinegroup.com</span>
        </li>
        <li class="contact__item">
          <svg class="contact__icon" viewBox="0 0 16 16"><circle cx="8" cy="8" r="7" fill="var(--red)"/><path d="M1 8h14M8 1c-3 3-3 11 0 14M8 1c3 3 3 11 0 14" fill="none" stroke="var(--white)" stroke-width="1"/></svg>
          <span>www.varkoworks.com</span>
        </li>
      </ul>
    </div>
  </section>

</main>
</body>
</html>
```